Bright Harbor Web Design & Marketing

Will award a 2nd place prize of $100.00 if someone can come up with a logo to match this design!
Updates

Okay, I'm really looking to see some better designs here. What do you think will bring the best designs out? Please remember with all future submissions I'm looking for a cartoon style / illustrator style website. I'm not sure what the technical term is for it, so I uploaded some images in the brief.

Target Market(s)

Small Business Owners

Industry/Entity Type

Marketing

Logo Text

BrightHarbor.com

Number of Pages Required

1 page

Colors

Designer to choose colors to be used in the design.

Requirements
Must have
• Logo should say BrightHarbor.com I would like more than just a text logo. I want some sort of cool custom graphic / icon with it that will look nice on shirts/hats/etc

```html
<!DOCTYPE html>
<html lang="en">
<head>
<meta charset="utf-8">
<title>Bright Harbor Web Design & Marketing</title>
<link href="https://fonts.googleapis.com/css2?family=Jost:wght@400;500;600;700&family=Open+Sans:wght@400;600;700&display=swap" rel="stylesheet">
<style>
:root{
  --navy:#26187a;
  --navy-dark:#1b1160;
  --sky:#a8dbee;
  --sky-light:#c5e8f5;
  --grey-bar:#6b6b6b;
  --grey-bg:#efefef;
  --ink:#2b2b2b;
  --muted:#6e6e6e;
  --line:#dcdcdc;
  --white:#ffffff;
  --star:#f2b01e;
}
*{box-sizing:border-box;margin:0;padding:0}
html,body{width:1200px;height:4380px;overflow:hidden}
body{font-family:"Open Sans",Arial,sans-serif;color:var(--ink);background:var(--white);position:relative}
section,header,footer,nav{position:absolute;left:0;width:1200px}
h2.section-title{font-family:"Jost",Arial,sans-serif;font-weight:500;font-size:26px;text-align:center;letter-spacing:1px;color:var(--ink);text-transform:uppercase}
h2.section-title b{color:var(--navy);font-weight:700}
.title-rule{width:60px;height:2px;background:var(--navy);margin:10px auto 0}

/* header */
.site-header{top:0;height:88px;background:var(--white)}
.brand{position:absolute;left:140px;top:16px;display:flex;align-items:center;gap:12px}
.brand-mark{width:52px;height:52px;background:var(--navy);border-radius:4px}
.brand-name{font-family:"Jost",sans-serif;font-weight:700;font-size:19px;line-height:21px;color:var(--navy);text-transform:uppercase;white-space:nowrap}
.header-phone{position:absolute;left:720px;top:26px;display:flex;align-items:center;gap:10px;font-size:19px;color:var(--ink)}
.header-cta{position:absolute;left:900px;top:26px;width:160px;height:34px;border-radius:17px;background:var(--navy);color:var(--white);font-size:12px;font-weight:700;text-align:center;line-height:34px;text-transform:uppercase}

.main-nav{top:88px;height:34px;background:var(--grey-bar)}
.main-nav ul{list-style:none;display:flex;justify-content:space-between;width:920px;margin:0 auto;height:34px}
.main-nav li{font-family:"Jost",sans-serif;font-size:13px;font-weight:600;color:var(--white);line-height:34px;padding:0 40px;text-transform:uppercase}
.main-nav li.active{background:var(--navy)}

/* hero */
.hero{top:122px;height:468px;background:var(--sky)}
.hero-title{position:absolute;left:146px;top:160px;z-index:2;font-family:"Jost",sans-serif;font-weight:600;font-size:25px;line-height:34px;color:var(--ink);white-space:nowrap}
.hero-dots{position:absolute;left:146px;top:322px;display:flex;gap:6px}
.hero-dots span{width:12px;height:7px;border-radius:4px;background:#5b5b7a}
.hero-dots span+span{background:#9aa3b4}
.hero-art{position:absolute;left:600px;top:50px;width:480px;height:380px;border-radius:8px;background:linear-gradient(135deg,var(--sky-light),#8fcbe3)}

/* about */
.about{top:590px;height:263px;background:var(--white)}
.about h2{padding-top:62px}
.about p{width:920px;margin:22px auto 0;font-size:13px;line-height:20px;text-align:center;color:var(--ink)}
.about p+p{margin-top:12px}

/* services */
.services{top:853px;height:671px;background:var(--grey-bg)}
.services h2{padding-top:60px}
.service-grid{position:absolute;left:140px;top:135px;display:grid;grid-template-columns:repeat(3,294px);gap:22px 19px}
.service-card{height:146px;background:var(--white);box-shadow:0 2px 6px rgba(0,0,0,.12);padding:24px 20px;display:flex;gap:16px}
.service-card svg{flex:0 0 44px}
.service-card h3{font-family:"Jost",sans-serif;font-weight:500;font-size:16px;line-height:18px;color:var(--ink)}
.service-card p{margin-top:10px;font-size:11px;line-height:15px;color:var(--muted)}

/* cta */
.cta-band{top:1524px;height:263px;background:linear-gradient(90deg,#0f1220,#2a2f44 45%,#13172a)}
.cta-band p{position:absolute;left:160px;top:80px;width:880px;text-align:center;color:var(--white);font-size:16px;line-height:24px}
.cta-button{position:absolute;left:520px;top:150px;width:160px;height:32px;border-radius:16px;background:var(--navy);color:var(--white);font-size:12px;font-weight:700;text-align:center;line-height:32px}

/* different */
.different{top:1787px;height:368px;background:var(--white)}
.different h2{padding-top:58px}
.feature-row{position:absolute;left:160px;top:136px;display:flex;gap:20px}
.feature{width:205px;text-align:center}
.feature-icon{width:76px;height:76px;border-radius:50%;border:3px solid var(--navy);margin:0 auto;display:flex;align-items:center;justify-content:center}
.feature h3{font-family:"Jost",sans-serif;font-weight:500;font-size:15px;line-height:18px;margin-top:18px;color:var(--ink)}
.feature p{font-size:11px;line-height:14px;color:var(--muted);margin-top:8px}

/* portfolio */
.portfolio{top:2155px;height:575px;background:var(--grey-bg)}
.portfolio h2{padding-top:58px}
.filter-tabs{position:absolute;left:0;width:1200px;top:122px;display:flex;justify-content:center;gap:8px}
.filter-tabs span{font-size:12px;padding:4px 14px;background:var(--white);border:1px solid var(--line);color:var(--ink)}
.filter-tabs span.active{background:var(--navy);color:var(--white);border-color:var(--navy)}
.work-grid{position:absolute;left:140px;top:180px;display:grid;grid-template-columns:repeat(4,218px);gap:18px 16px}
.work-item{height:165px;border:4px solid var(--white);box-shadow:0 2px 6px rgba(0,0,0,.12)}

/* team */
.team{top:2730px;height:599px;background:var(--white)}
.team h2{padding-top:62px}
.team-row{position:absolute;left:172px;top:132px;display:flex;gap:26px}
.member{width:150px;height:210px;background:var(--white);box-shadow:0 2px 6px rgba(0,0,0,.18);text-align:center;position:relative}
.member-photo{width:90px;height:90px;border-radius:50%;margin:18px auto 0;background:linear-gradient(160deg,#c9d2df,#8797b0)}
.member h3{font-family:"Jost",sans-serif;font-weight:500;font-size:15px;margin-top:12px}
.member p{font-size:11px;color:var(--muted);margin-top:2px}
.member-social{position:absolute;left:0;bottom:0;width:150px;height:34px;background:var(--grey-bar);display:flex;justify-content:center;align-items:center;gap:6px}
.member.active .member-social{background:var(--navy)}
.member-social i{width:18px;height:18px;border-radius:50%;border:1.5px solid var(--white)}
.slider-arrow{position:absolute;width:22px;height:22px;border-radius:50%;border:1px solid #bbb;display:flex;align-items:center;justify-content:center}
.team-bio{position:absolute;left:140px;top:360px;width:920px;height:200px;box-shadow:0 2px 6px rgba(0,0,0,.14);padding:22px 20px;font-size:12px;line-height:16px;color:var(--muted);text-align:center}
.team-bio p+p{margin-top:16px}

/* reviews */
.reviews{top:3329px;height:423px;background:var(--grey-bg)}
.reviews h2{padding-top:58px}
.review{position:absolute;top:140px;width:440px;display:flex;gap:18px}
.reviewer{width:90px;text-align:center}
.reviewer-photo{width:70px;height:70px;border-radius:50%;margin:0 auto;background:linear-gradient(160deg,#c9d2df,#7a8aa5)}
.reviewer b{display:block;font-size:12px;margin-top:6px}
.stars{color:var(--star);font-size:11px;letter-spacing:1px}
.review p{font-size:11px;line-height:15px;color:var(--muted);font-style:italic;width:320px}
.review-track{position:absolute;left:140px;top:300px;width:920px;height:1px;background:#999}
.review-dot{position:absolute;left:592px;top:292px;width:16px;height:16px;border-radius:50%;background:var(--navy)}

/* clients */
.clients{top:3752px;height:263px;background:var(--white)}
.clients h2{padding-top:56px}
.client-row{position:absolute;left:140px;top:120px;display:flex;gap:15px}
.client{width:141px;height:78px;border:1px solid var(--line);display:flex;align-items:center;justify-content:center;gap:6px;font-family:"Open Sans",sans-serif;font-weight:700;font-size:16px;color:#333}
.client i{width:14px;height:14px;background:#333}

/* newsletter */
.newsletter{top:4015px;height:53px;background:var(--navy-dark)}
.newsletter-title{position:absolute;left:196px;top:14px;font-family:"Jost",sans-serif;font-weight:600;font-size:17px;color:var(--white);letter-spacing:.5px}
.newsletter-icon{position:absolute;left:140px;top:4px;width:44px;height:44px;border-radius:6px;background:#f29a3a}
.newsletter-form{position:absolute;left:548px;top:13px;display:flex}
.newsletter-form span{width:395px;height:28px;background:var(--white);font-size:11px;color:#999;line-height:28px;padding-left:10px}
.newsletter-form b{width:115px;height:28px;background:#555;color:var(--white);font-size:12px;line-height:28px;text-align:center}

/* footer */
.site-footer{top:4068px;height:277px;background:linear-gradient(180deg,#2b2c36,#1a1b23)}
.footer-col{position:absolute;top:28px}
.footer-col h4{font-family:"Jost",sans-serif;font-weight:600;font-size:14px;color:var(--white);text-transform:uppercase;margin-bottom:14px}
.footer-col li{list-style:none;font-size:12px;color:#d6d6d6;line-height:22px}
.footer-col li::before{content:"› ";color:#aaa}
.contact-line{display:flex;gap:8px;font-size:12px;color:#d6d6d6;line-height:16px;margin-bottom:12px}
.contact-line i{width:12px;height:12px;border-radius:50%;background:#bbb;flex:0 0 12px;margin-top:2px}
.field{width:190px;height:24px;background:var(--white);font-size:10px;color:#999;padding:5px 8px;margin-bottom:7px}
.field.tall{height:48px}
.submit{width:70px;height:22px;background:var(--navy);color:var(--white);font-size:10px;font-weight:700;text-align:center;line-height:22px}
.footer-brand{position:absolute;left:900px;top:60px;width:160px;display:flex;flex-direction:column;align-items:center;gap:10px;font-family:"Jost",sans-serif;font-weight:700;font-size:20px;line-height:24px;color:var(--white);text-transform:uppercase;text-align:center}
.footer-brand span.mark{width:56px;height:56px;border:4px solid var(--white);border-radius:4px}
.footer-social{position:absolute;left:938px;top:200px;display:flex;gap:6px}
.footer-social i{width:20px;height:20px;border-radius:50%;background:#3b6fc7}
.copyright{position:absolute;left:0;width:1200px;top:4345px;height:35px;background:#101116;color:#bbb;font-size:11px;text-align:center;line-height:35px}
</style>
</head>
<body>

<header class="site-header">
  <div class="brand">
    <span class="brand-mark"></span>
    <span class="brand-name">Bright Harbor<br>Web Design</span>
  </div>
  <div class="header-phone">
    <svg width="26" height="26" viewBox="0 0 26 26"><circle cx="13" cy="13" r="12" fill="none" stroke="#2b2b2b" stroke-width="1.5"/><path d="M9 7c1 0 2 3 2 3l-1.5 1.5c.8 1.8 2.2 3.2 4 4L15 14s3 1 3 2-1.5 2.5-2.5 2.5C11 18.5 7.5 15 7.5 10.5 7.5 9 8 7 9 7z" fill="#2b2b2b"/></svg>
    123.456.7890
  </div>
  <div class="header-cta">Contact us now</div>
</header>

<nav class="main-nav">
  <ul>
    <li class="active">Home</li>
    <li>Services &amp; Pricing</li>
    <li>Our Team</li>
    <li>Clients/Portfolio</li>
    <li>Contact Us</li>
  </ul>
</nav>

<section class="hero">
  <div class="hero-art" role="img" aria-label="Flat illustration of a search bar, magnifying glass, charts, location pins and a laptop with growth graphs"></div>
  <h1 class="hero-title">The Design &amp; Marketing Team<br>That Always Puts Trust &amp;<br>Loyalty Before Profits</h1>
  <div class="hero-dots"><span></span><span></span><span></span></div>
</section>

<section class="about">
  <h2 class="section-title">About <b>Bright Harbor</b> Web Design</h2>
  <p>We believe that honesty and integrity come before personal profits. We are a family owned and operated company. Our parents raised us to take care of each other and that's exactly what we've done. We treat each of our clients with the same loyalty and respect that we give each other.</p>
  <p>We are not looking to have hundreds and hundreds of clients. We are looking to expand our family with a handful of like-minded individuals. Companies who take pride in their work and their customers. We want to build mutually beneficial, lucrative, and long term partnerships.</p>
</section>

<section class="services">
  <h2 class="section-title">Our <b>Services</b></h2>
  <div class="title-rule"></div>
  <div class="service-grid">
    <div class="service-card">
      <svg width="44" height="44" viewBox="0 0 44 44"><rect x="4" y="8" width="36" height="24" rx="2" fill="none" stroke="#26187a" stroke-width="3"/><path d="M16 38h12M22 32v6" stroke="#26187a" stroke-width="3"/></svg>
      <div><h3>Website Design<br>&amp; Management</h3><p>Lorem ipsum dolor sit amet, consectetur adipiscing elit, sed diam nonummy nibh euismod tincidunt ut laoreet.</p></div>
    </div>
    <div class="service-card">
      <svg width="44" height="44" viewBox="0 0 44 44"><path d="M8 36l4-12 20-20 8 8-20 20z" fill="none" stroke="#26187a" stroke-width="3"/><path d="M12 24l8 8" stroke="#26187a" stroke-width="3"/></svg>
      <div><h3>Logo Design<br>&amp; Branding Materials</h3><p>Lorem ipsum dolor sit amet, consectetur adipiscing elit, sed diam nonummy nibh euismod tincidunt ut laoreet.</p></div>
    </div>
    <div class="service-card">
      <svg width="44" height="44" viewBox="0 0 44 44"><path d="M4 8h6l5 20h20l4-14H13" fill="none" stroke="#26187a" stroke-width="3"/><circle cx="17" cy="35" r="3" fill="#26187a"/><circle cx="32" cy="35" r="3" fill="#26187a"/></svg>
      <div><h3>Online Store Design<br>&amp; Management</h3><p>Lorem ipsum dolor sit amet, consectetur adipiscing elit, sed diam nonummy nibh euismod tincidunt ut laoreet.</p></div>
    </div>
    <div class="service-card">
      <svg width="44" height="44" viewBox="0 0 44 44"><path d="M22 40S9 26 9 17a13 13 0 0126 0c0 9-13 23-13 23z" fill="none" stroke="#26187a" stroke-width="3"/><circle cx="22" cy="17" r="5" fill="#26187a"/></svg>
      <div><h3>Local<br>SEO Management</h3><p>Lorem ipsum dolor sit amet, consectetur adipiscing elit, sed diam nonummy nibh euismod tincidunt ut laoreet.</p></div>
    </div>
    <div class="service-card">
      <svg width="44" height="44" viewBox="0 0 44 44"><circle cx="18" cy="18" r="12" fill="none" stroke="#26187a" stroke-width="3"/><path d="M27 27l12 12" stroke="#26187a" stroke-width="4"/></svg>
      <div><h3>Search Engine<br>Optimization</h3><p>Lorem ipsum dolor sit amet, consectetur adipiscing elit, sed diam nonummy nibh euismod tincidunt ut laoreet.</p></div>
    </div>
    <div class="service-card">
      <svg width="44" height="44" viewBox="0 0 44 44"><circle cx="10" cy="22" r="5" fill="#26187a"/><circle cx="33" cy="10" r="5" fill="#26187a"/><circle cx="33" cy="34" r="5" fill="#26187a"/><path d="M10 22L33 10M10 22l23 12" stroke="#26187a" stroke-width="2.5"/></svg>
      <div><h3>Social Media<br>Marketing</h3><p>Lorem ipsum dolor sit amet, consectetur adipiscing elit, sed diam nonummy nibh euismod tincidunt ut laoreet.</p></div>
    </div>
    <div class="service-card">
      <svg width="44" height="44" viewBox="0 0 44 44"><rect x="6" y="6" width="32" height="32" fill="none" stroke="#26187a" stroke-width="3"/><path d="M12 14h20M12 22h20M12 30h12" stroke="#26187a" stroke-width="3"/></svg>
      <div><h3>Marketing<br>Material &amp; Print Design</h3><p>Lorem ipsum dolor sit amet, consectetur adipiscing elit, sed diam nonummy nibh euismod tincidunt ut laoreet.</p></div>
    </div>
    <div class="service-card">
      <svg width="44" height="44" viewBox="0 0 44 44"><rect x="6" y="12" width="32" height="24" rx="2" fill="none" stroke="#26187a" stroke-width="3"/><path d="M16 12V7h12v5M6 22h32" stroke="#26187a" stroke-width="3"/></svg>
      <div><h3>Outsourcing<br>Management</h3><p>Lorem ipsum dolor sit amet, consectetur adipiscing elit, sed diam nonummy nibh euismod tincidunt ut laoreet.</p></div>
    </div>
    <div class="service-card">
      <svg width="44" height="44" viewBox="0 0 44 44"><circle cx="14" cy="14" r="6" fill="#26187a"/><circle cx="30" cy="14" r="6" fill="#26187a"/><path d="M4 36c0-8 4-12 10-12s10 4 10 12zM20 36c0-8 4-12 10-12s10 4 10 12z" fill="#26187a"/></svg>
      <div><h3>Consulting<br>Service</h3><p>Lorem ipsum dolor sit amet, consectetur adipiscing elit, sed diam nonummy nibh euismod tincidunt ut laoreet.</p></div>
    </div>
  </div>
</section>

<section class="cta-band">
  <p>Lorem ipsum dolor sit amet, consectetur adipiscing elit, sed diam nonummy nibh euismod tincidunt ut laoreet dolore magna aliquam erat volutpat. Ut wisi enim ad minim veniam, quis nostrud exerci tation ullamcorper.</p>
  <div class="cta-button">CONTACT US NOW »</div>
</section>

<section class="different">
  <h2 class="section-title">What Makes <b>Me Different?</b></h2>
  <div class="feature-row">
    <div class="feature">
      <div class="feature-icon"><svg width="40" height="40" viewBox="0 0 40 40"><path d="M20 4L37 34H3z" fill="none" stroke="#26187a" stroke-width="3"/><path d="M20 15v9" stroke="#26187a" stroke-width="3"/><circle cx="20" cy="29" r="2" fill="#26187a"/></svg></div>
      <h3>100% Risk Free<br>Investment</h3>
      <p>If we are unable to deliver anything that we say we can we will refund you 100% of your investment.</p>
    </div>
    <div class="feature">
      <div class="feature-icon"><svg width="40" height="40" viewBox="0 0 40 40"><rect x="4" y="9" width="32" height="22" rx="3" fill="none" stroke="#26187a" stroke-width="3"/><path d="M4 16h32" stroke="#26187a" stroke-width="4"/></svg></div>
      <h3>Customer Loyalty<br>Program</h3>
      <p>After 12 months of on time payments, customers will receive cash back reward bonuses.</p>
    </div>
    <div class="feature">
      <div class="feature-icon"><svg width="40" height="40" viewBox="0 0 40 40"><circle cx="20" cy="13" r="7" fill="#26187a"/><path d="M7 36c0-9 6-13 13-13s13 4 13 13z" fill="#26187a"/></svg></div>
      <h3>Unmatched Personal<br>Service</h3>
      <p>Do you need us to come to your office to help train staff on the management of your new site?</p>
    </div>
    <div class="feature">
      <div class="feature-icon"><svg width="40" height="40" viewBox="0 0 40 40"><rect x="4" y="9" width="32" height="22" rx="3" fill="none" stroke="#26187a" stroke-width="3"/><circle cx="20" cy="20" r="5" fill="none" stroke="#26187a" stroke-width="2.5"/></svg></div>
      <h3>Multiple Payment<br>Options Available</h3>
      <p>Website Leasing, 90 Days Same As Cash, Website Financing</p>
    </div>
  </div>
</section>

<section class="portfolio">
  <h2 class="section-title">Work <b>Portfolio</b></h2>
  <div class="title-rule"></div>
  <div class="filter-tabs">
    <span class="active">All</span><span>Website Design</span><span>Logo Design And Branding Materials</span><span>Local Seo Management</span>
  </div>
  <div class="work-grid">
    <div class="work-item" role="img" aria-label="Website mockup with a sports hero image" style="background:linear-gradient(135deg,#e8e8e8,#b9b9b9)"></div>
    <div class="work-item" role="img" aria-label="Orange stationery and branding set" style="background:linear-gradient(135deg,#f1a24a,#2f3a55)"></div>
    <div class="work-item" role="img" aria-label="Logo presentation on a dark textured background" style="background:linear-gradient(135deg,#6f6f6f,#3d3d3d)"></div>
    <div class="work-item" role="img" aria-label="Local SEO map illustration with pins" style="background:linear-gradient(135deg,#2ba7c9,#1d7f9e)"></div>
    <div class="work-item" role="img" aria-label="Colourful letter logo concept on white" style="background:linear-gradient(135deg,#f6f6f6,#dfe7f3)"></div>
    <div class="work-item" role="img" aria-label="Blue marketing illustration with charts" style="background:linear-gradient(135deg,#2f8fd8,#1a5fa8)"></div>
    <div class="work-item" role="img" aria-label="Responsive website shown on several devices" style="background:linear-gradient(135deg,#3a3a3a,#d6552c)"></div>
    <div class="work-item" role="img" aria-label="White business card and stationery mockup" style="background:linear-gradient(135deg,#f2f2f2,#9a9a9a)"></div>
  </div>
</section>

<section class="team">
  <h2 class="section-title">Our <b>Team</b></h2>
  <div class="title-rule"></div>
  <div class="slider-arrow" style="left:92px;top:228px"><svg width="8" height="10" viewBox="0 0 8 10"><path d="M6 1L2 5l4 4" fill="none" stroke="#888" stroke-width="1.5"/></svg></div>
  <div class="slider-arrow" style="left:1086px;top:228px"><svg width="8" height="10" viewBox="0 0 8 10"><path d="M2 1l4 4-4 4" fill="none" stroke="#888" stroke-width="1.5"/></svg></div>
  <div class="team-row">
    <div class="member active"><div class="member-photo" role="img" aria-label="Portrait photo of team member"></div><h3>Owen Marlow</h3><p>Chief Executive Officer</p><div class="member-social"><i></i><i></i><i></i><i></i></div></div>
    <div class="member"><div class="member-photo" role="img" aria-label="Portrait photo of team member"></div><h3>Owen Marlow</h3><p>Chief Operations Officer</p><div class="member-social"><i></i><i></i><i></i><i></i></div></div>
    <div class="member"><div class="member-photo" role="img" aria-label="Portrait photo of team member"></div><h3>Owen Marlow</h3><p>Chief Technical Officer</p><div class="member-social"><i></i><i></i><i></i><i></i></div></div>
    <div class="member"><div class="member-photo" role="img" aria-label="Portrait photo of team member"></div><h3>Owen Marlow</h3><p>Finance</p><div class="member-social"><i></i><i></i><i></i><i></i></div></div>
    <div class="member"><div class="member-photo" role="img" aria-label="Portrait photo of team member"></div><h3>Owen Marlow</h3><p>Chief Executive Officer</p><div class="member-social"><i></i><i></i><i></i><i></i></div></div>
  </div>
  <div class="team-bio">
    <p>Lorem ipsum dolor sit amet, consectetuer adipiscing elit, sed diam nonummy nibh euismod tincidunt ut laoreet dolore magna aliquam erat volutpat. Ut wisi enim ad minim veniam, quis nostrud exerci tation ullamcorper suscipit lobortis nisl ut aliquip ex ea commodo consequat. Duis autem vel eum iriure dolor in hendrerit in vulputate velit esse molestie consequat, vel illum dolore eu feugiat nulla facilisis at vero eros et accumsan et iusto odio dignissim qui blandit praesent luptatum zzril delenit augue duis dolore te feugait nulla facilisi.</p>
    <p>Lorem ipsum dolor sit amet, consectetuer adipiscing elit, sed diam nonummy nibh euismod tincidunt ut laoreet dolore magna aliquam erat volutpat. Ut wisi enim ad minim veniam, quis nostrud exerci tation ullamcorper suscipit lobortis nisl ut aliquip ex ea commodo consequat. Duis autem vel eum iriure dolor in hendrerit in vulputate velit esse molestie consequat, vel illum dolore eu feugiat nulla facilisis at vero eros et accumsan et iusto odio dignissim qui blandit praesent luptatum zzril delenit augue duis dolore te feugait nulla facilisi.</p>
  </div>
</section>

<section class="reviews">
  <h2 class="section-title">Client <b>Reviews</b></h2>
  <div class="review" style="left:140px">
    <div class="reviewer"><div class="reviewer-photo" role="img" aria-label="Client portrait"></div><b>Lorem Ipsum</b><span class="stars">★★★★★</span></div>
    <p>“ Lorem ipsum ut amet ca adipiscing elit sed nonummy nibh euismod tincidunt ut laoreet dolore magna aliquam erat volutpat. Ut wisi enim ad minim veniam quis nostrud exerci tation ullamcorper suscipit lobortis nisl ut aliquip ex ea commodo consequat duis autem vel eum iriure dolor in hendrerit ”</p>
  </div>
  <div class="review" style="left:620px">
    <div class="reviewer"><div class="reviewer-photo" role="img" aria-label="Client portrait"></div><b>Lorem Ipsum</b><span class="stars">★★★★★</span></div>
    <p>“ Lorem ipsum ut amet ca adipiscing elit sed nonummy nibh euismod tincidunt ut laoreet dolore magna aliquam erat volutpat. Ut wisi enim ad minim veniam quis nostrud exerci tation ullamcorper suscipit lobortis nisl ut aliquip ex ea commodo consequat duis autem vel eum iriure dolor in hendrerit ”</p>
  </div>
  <div class="review-track"></div>
  <div class="review-dot"></div>
</section>

<section class="clients">
  <h2 class="section-title">Our <b>Clients</b></h2>
  <div class="title-rule"></div>
  <div class="slider-arrow" style="left:92px;top:148px"><svg width="8" height="10" viewBox="0 0 8 10"><path d="M6 1L2 5l4 4" fill="none" stroke="#333" stroke-width="1.5"/></svg></div>
  <div class="slider-arrow" style="left:1086px;top:148px"><svg width="8" height="10" viewBox="0 0 8 10"><path d="M2 1l4 4-4 4" fill="none" stroke="#333" stroke-width="1.5"/></svg></div>
  <div class="client-row">
    <div class="client"><i></i>Ridgeline</div>
    <div class="client">Tallpine</div>
    <div class="client">Calderwood</div>
    <div class="client"><i style="border-radius:50%"></i>Northvale</div>
    <div class="client">Quillmark</div>
    <div class="client">Tallpine</div>
  </div>
</section>

<section class="newsletter">
  <div class="newsletter-icon"></div>
  <div class="newsletter-title">SUBSCRIBE OUR NEWSLETTER</div>
  <div class="newsletter-form"><span>Enter Your Email Address</span><b>SUBSCRIBE »</b></div>
</section>

<footer class="site-footer">
  <div class="footer-col" style="left:140px">
    <h4>Quick Links</h4>
    <ul><li>Home</li><li>Services &amp; Pricing</li><li>Our Team</li><li>Clients/Portfolio</li><li>Contact Us</li></ul>
  </div>
  <div class="footer-col" style="left:380px">
    <h4>Contact Details</h4>
    <div class="contact-line"><i></i><span>BRIGHT HARBOR WEB DESIGN<br>0000 Harbor Lane, Suite 12<br>Bayview, ST 00000</span></div>
    <div class="contact-line"><i></i><span>123.456.7890</span></div>
    <div class="contact-line"><i></i><span>123.456.7890</span></div>
    <div class="contact-line"><i></i><span>info@brightharbor.com</span></div>
  </div>
  <div class="footer-col" style="left:634px">
    <h4>Quick Inquiry</h4>
    <div class="field">Name</div>
    <div class="field">Email</div>
    <div class="field tall">Message</div>
    <div class="submit">SUBMIT »</div>
  </div>
  <div class="footer-brand"><span class="mark"></span>Bright Harbor</div>
  <div class="footer-social"><i></i><i></i><i></i><i></i></div>
</footer>

<div class="copyright">Copyright © 2017 BRIGHT HARBOR WEB DESIGN. All Rights Reserved.</div>

</body>
</html>
```